Business card for my new company (Accounting firm)

I need a business card for my new business Brightwell Advisory and Ledger SA. Our services are accounting, tax, audit and financial management. Our customers are small companies, start-ups and new companies. The final design has to show financial security, trust and growth. Please find our logo attached to the business card. Text for the business card: Brightwell Advisory and Ledger SA Tomas Varenholt Director and Founder Certified Accountant Tel. 022 418 57 34 tv@clairevalconseil.ch www.clairevalconseil.ch Rue des Vergières 27 1201 Geneva
Target Market(s)
Our customers are small companies, start-ups and new companies.
Industry/Entity Type
Finance And Accounting
Contact Information for Business Card
Claireval Conseil et Comptes SA
Tomas Varenholt
Directeur et Fondateur
Expert-comptable diplômé
Tél. 022 418 57 34
tv@clairevalconseil.ch
www.clairevalconseil.ch
Rue des Vergières 27
1201 Genève

```html
<!DOCTYPE html>
<html lang="fr">
<head>
<meta charset="utf-8">
<title>Claireval Conseil et Comptes SA — Carte de visite</title>
<link rel="stylesheet" href="https://fonts.googleapis.com/css2?family=Montserrat:wght@500;600&family=Roboto:wght@400;700&display=swap">
<style>
  :root {
    --page: #e4e6e8;
    --blue-light: #2a9fd4;
    --blue: #1f78b4;
    --blue-deep: #1a5f91;
    --paper: #f3f4f5;
    --ink: #3a3d40;
    --arc: #2e3033;
    --white: #ffffff;
  }
  * { box-sizing: border-box; margin: 0; padding: 0; }
  html, body {
    width: 1200px; height: 726px; overflow: hidden;
    background: var(--page);
  }
  .sheet {
    position: relative; width: 1200px; height: 726px;
    display: flex; align-items: center; justify-content: center; gap: 50px;
  }
  .card {
    position: relative; width: 520px; height: 336px; overflow: hidden;
    border-radius: 3px;
    box-shadow: 0 6px 18px rgba(0,0,0,.18);
  }

  /* Front */
  .card--front {
    background: linear-gradient(160deg, var(--blue-light) 0%, var(--blue) 55%, var(--blue-deep) 100%);
    color: var(--white);
  }
  .front-name {
    position: absolute; left: 0; right: 0; top: 128px; text-align: center;
    font-family: "Montserrat", sans-serif; font-weight: 500;
    font-size: 30px; letter-spacing: 2px; line-height: 1.2;
  }
  .front-web {
    position: absolute; left: 0; right: 0; bottom: 46px; text-align: center;
    font-family: "Roboto", sans-serif; font-weight: 700; font-size: 15px;
  }

  /* Back */
  .card--back { background: var(--paper); }
  .back-shape { position: absolute; inset: 0; }
  .back-brand {
    position: absolute; left: 28px; top: 138px; width: 220px;
    display: flex; align-items: center; gap: 10px;
  }
  .brand-dot {
    flex: none; width: 22px; height: 22px; border-radius: 50%;
    background: var(--blue);
  }
  .brand-name {
    font-family: "Montserrat", sans-serif; font-weight: 600;
    font-size: 21px; line-height: 1.15; color: var(--ink);
  }
  .back-details {
    position: absolute; right: 26px; top: 34px; text-align: right;
    font-family: "Roboto", sans-serif; color: var(--white);
  }
  .person-name { font-weight: 700; font-size: 20px; margin-bottom: 4px; }
  .person-role { font-size: 11.5px; line-height: 1.4; }
  .address { margin-top: 34px; font-size: 13.5px; line-height: 1.4; }
  .contact { list-style: none; font-size: 13.5px; line-height: 1.45; }
  .contact li { display: flex; justify-content: flex-end; align-items: center; gap: 8px; }
  .contact svg { width: 12px; height: 12px; flex: none; }
  .icon-gap { width: 12px; display: inline-block; }
</style>
</head>
<body>
<main class="sheet">
  <section class="card card--front" aria-label="Recto">
    <p class="front-name">Claireval Conseil<br>et Comptes</p>
    <p class="front-web">www.clairevalconseil.ch</p>
  </section>

  <section class="card card--back" aria-label="Verso">
    <svg class="back-shape" viewBox="0 0 520 336" aria-hidden="true">
      <defs>
        <linearGradient id="panelBlue" x1="0" y1="0" x2="1" y2="1">
          <stop offset="0" stop-color="#1a5f91"/>
          <stop offset="1" stop-color="#1f78b4"/>
        </linearGradient>
      </defs>
      <path d="M250 0 Q340 168 262 336 L520 336 L520 0 Z" fill="url(#panelBlue)"/>
      <path d="M250 0 Q340 168 262 336" fill="none" stroke="var(--arc)" stroke-width="9"/>
    </svg>

    <div class="back-brand">
      <span class="brand-dot"></span>
      <span class="brand-name">Claireval Conseil et Comptes</span>
    </div>

    <div class="back-details">
      <p class="person-name">Tomas Varenholt</p>
      <p class="person-role">Directeur et Fondateur<br>Expert-comptable diplômé</p>
      <p class="address">Rue des Vergières 27<span class="icon-gap"></span><br>1201 Genève<span class="icon-gap"></span></p>
      <ul class="contact">
        <li>022 418 57 34
          <svg viewBox="0 0 12 12" aria-label="Téléphone"><path d="M2 1.5h2l1 2.5-1.3 1a6 6 0 0 0 3.3 3.3l1-1.3 2.5 1v2a1 1 0 0 1-1 1A9 9 0 0 1 1 2.5a1 1 0 0 1 1-1z" fill="#fff"/></svg>
        </li>
        <li>tv@clairevalconseil.ch
          <svg viewBox="0 0 12 12" aria-label="Courriel"><rect x="0.5" y="2.5" width="11" height="7" fill="#fff"/><path d="M0.5 2.5 6 6.8 11.5 2.5" fill="none" stroke="#1a5f91" stroke-width="1"/></svg>
        </li>
        <li>www.clairevalconseil.ch
          <svg viewBox="0 0 12 12" aria-label="Site web"><circle cx="6" cy="6" r="5.2" fill="none" stroke="#fff" stroke-width="1.2"/><ellipse cx="6" cy="6" rx="2.2" ry="5.2" fill="none" stroke="#fff" stroke-width="1"/><path d="M0.8 6h10.4" stroke="#fff" stroke-width="1"/></svg>
        </li>
      </ul>
    </div>
  </section>
</main>
</body>
</html>
```